Coastline Premier Retreats Business Card Design

Design a business card for Coastline Premier Retreats. Look at the website for colors and reference. Card should have logo, name, title, office number, mobile number, email, URL and a tagline like, "Luxury Hotel & Resort Email Marketing" (This might change).

https://www.coastlinepremierretreats.example

The rest I will leave up to your imagination.

Contact Information for Business Card

Logo, name, title, office number, mobile number, email, URL and a tagline like, "Luxury Hotel & Resort Email Marketing" (This might change).

```html
<!DOCTYPE html>
<html lang="en">
<head>
<meta charset="utf-8">
<title>Coastline Premier Retreats – Business Card</title>
<link href="https://fonts.googleapis.com/css2?family=Lato:wght@400;700;900&display=swap" rel="stylesheet">
<style>
  :root {
    --stage: #3a3b3e;
    --card-white: #ffffff;
    --card-black: #151515;
    --accent: #f47216;
    --ink: #1a1a1a;
    --muted: #555555;
    --on-accent: #ffffff;
  }
  * { box-sizing: border-box; margin: 0; padding: 0; }
  html, body { width: 1200px; height: 952px; overflow: hidden; }
  body {
    background: var(--stage);
    font-family: "Lato", sans-serif;
    position: relative;
  }
  .card {
    position: absolute;
    width: 540px;
    height: 310px;
    border-radius: 24px;
    overflow: hidden;
  }
  .card--front { left: 40px; top: 420px; background: var(--card-white); color: var(--ink); }
  .card--back { left: 620px; top: 190px; background: var(--card-black); color: var(--on-accent); }

  .accent-band {
    position: absolute;
    left: 0; right: 0;
    top: 238px;
    height: 34px;
    background: var(--accent);
    color: var(--on-accent);
    display: flex;
    align-items: center;
    padding-left: 34px;
    font-size: 14px;
    letter-spacing: 0.6px;
  }

  .brand {
    position: absolute;
    display: flex;
    align-items: center;
    gap: 10px;
    font-weight: 900;
    text-transform: uppercase;
    letter-spacing: 1px;
    white-space: nowrap;
  }
  .brand__mark { width: 14px; height: 14px; background: var(--accent); flex: none; }
  .card--front .brand { left: 150px; top: 34px; font-size: 19px; color: var(--ink); }
  .card--back .brand { left: 50%; top: 104px; transform: translateX(-50%); font-size: 22px; color: var(--on-accent); }

  .holder { position: absolute; left: 34px; top: 100px; }
  .holder__name { font-size: 19px; letter-spacing: 0.5px; text-transform: uppercase; font-weight: 400; }
  .holder__surname { color: var(--accent); font-weight: 900; }
  .holder__title { margin-top: 6px; font-size: 14px; color: var(--muted); }

  .contact { position: absolute; left: 250px; top: 100px; list-style: none; }
  .contact li { display: flex; align-items: center; gap: 9px; font-size: 13px; color: var(--ink); margin-bottom: 11px; }
  .contact svg { width: 18px; height: 18px; flex: none; }
</style>
</head>
<body>

<section class="card card--front" aria-label="Business card front">
  <div class="brand"><span class="brand__mark"></span>Coastline Premier Retreats</div>

  <div class="holder">
    <p class="holder__name">Daniel R. <span class="holder__surname">Whitford</span></p>
    <p class="holder__title">Managing Director</p>
  </div>

  <ul class="contact">
    <li>
      <svg viewBox="0 0 18 18"><rect width="18" height="18" rx="3" fill="#1a1a1a"/><path d="M5.5 4.5l2 .3.8 2.3-1.2 1a6 6 0 0 0 2.8 2.8l1-1.2 2.3.8.3 2c-4.6.6-8.6-3.4-8-8z" fill="#fff"/></svg>
      +00 555 010 24
    </li>
    <li>
      <svg viewBox="0 0 18 18"><rect width="18" height="18" rx="3" fill="#1a1a1a"/><rect x="4" y="5.5" width="10" height="7" fill="none" stroke="#fff" stroke-width="1.2"/><path d="M4 5.5l5 4 5-4" fill="none" stroke="#fff" stroke-width="1.2"/></svg>
      hello@coastlinepremierretreats.example
    </li>
    <li>
      <svg viewBox="0 0 18 18"><rect width="18" height="18" rx="3" fill="#1a1a1a"/><circle cx="9" cy="9" r="4.8" fill="none" stroke="#fff" stroke-width="1.2"/><path d="M4.2 9h9.6M9 4.2c-2.4 2.6-2.4 7 0 9.6M9 4.2c2.4 2.6 2.4 7 0 9.6" fill="none" stroke="#fff" stroke-width="1"/></svg>
      www.coastlinepremierretreats.example
    </li>
  </ul>

  <div class="accent-band">2210 Harbor View Lane Seaside, DC 20091</div>
</section>

<section class="card card--back" aria-label="Business card back">
  <div class="brand"><span class="brand__mark"></span>Coastline Premier Retreats</div>
  <div class="accent-band">Luxury Hotel &amp; Resort Email Marketing</div>
</section>

</body>
</html>
```